The Marigold Venture WEBSITE DESIGN

Marigold is a not for profit working in international aid and development. The website needs to be lively not depressing,earthy rather than bling, have a dramatic impact over lightweight. It may be that a black and white with spot colour may be more impacting given the simplicity I want for the site. Marigold works in partnership with registered NGOs in Asia and Africa. At any one time it will have about five feature projects. The purpose is for people to be able to find out about the projects, the countries, the partner organisations, people's stories and then give people the opportunity to give their financial and volunteer support.

Target Market(s)

First World Donors
All ages but particularly 25 - 55

Industry/Entity Type

Human Rights

Number of Pages Required

5+ page

Font styles to use
Sans Serif

Requirements
Must have
• Simplicity
• Easy access to giving options
• Highlight stories both video and image + copy (sample in attachments)
• Lots of images over copy
Nice to have
• Interest
• Not boring
• May work in black and white with a spot colour or sepia look
Should not have
• Shiny new look
• Dont know how many pages or if it be coded or uncoded - makes no sense to me

```html
<!DOCTYPE html>
<html lang="en">
<head>
<meta charset="utf-8">
<title>The Marigold Venture</title>
<link href="https://fonts.googleapis.com/css2?family=Roboto:wght@300;400;500;700&display=swap" rel="stylesheet">
<style>
:root{
  --ink:#1e1e1e;
  --dark:#2a2a2a;
  --band:#333333;
  --mid:#8a8a8a;
  --line:#d6d6d6;
  --soft:#f0f0f0;
  --paper:#ffffff;
  --text:#555555;
}
*{box-sizing:border-box;margin:0;padding:0}
html,body{width:761px;height:1200px;overflow:hidden}
body{font-family:"Roboto",Arial,sans-serif;color:var(--text);
  background:linear-gradient(90deg,#9a9a9a 0,#e9e9e9 2.5%,#fff 2.7%,#fff 97.3%,#e9e9e9 97.5%,#9a9a9a 100%);}
.page{position:relative;width:721px;height:1200px;margin:0 auto;background:var(--paper)}
/* header */
.site-header{position:absolute;left:0;top:0;width:100%;height:64px}
.brand{position:absolute;left:8px;top:8px;display:flex;flex-direction:column;align-items:center;width:78px}
.brand-mark{width:22px;height:22px;border-radius:50%;background:var(--ink)}
.brand-name{font-size:12px;font-weight:700;letter-spacing:1.5px;color:var(--ink);margin-top:4px}
.brand-sub{font-size:6px;letter-spacing:2px;color:var(--ink)}
.main-nav{position:absolute;right:0;top:10px;height:24px;width:540px;background:var(--dark);display:flex;align-items:center;padding-left:24px;gap:16px}
.main-nav a{font-size:8px;color:#ddd;text-decoration:none;text-transform:uppercase;letter-spacing:.4px}
.main-nav a.active{background:#fff;color:var(--ink);padding:4px 8px;font-weight:500}
.social{margin-left:auto;display:flex;gap:5px;padding-right:10px}
.social span{width:14px;height:14px;border-radius:50%;border:1.5px solid #ddd;display:block}
/* hero */
.hero{position:absolute;left:0;top:64px;width:100%;height:266px;
  background:
    linear-gradient(90deg,rgba(40,60,50,.25) 0,rgba(0,0,0,0) 20%,rgba(120,40,40,.15) 45%,rgba(0,0,0,0) 70%,rgba(50,70,110,.2) 100%),
    linear-gradient(180deg,#a29c8c 0,#7b7a6c 25%,#5a4c3e 45%,#9c5a34 62%,#6f5338 80%,#4a463f 100%)}
/* section titles */
.section-title{font-size:13px;font-weight:500;text-transform:uppercase;color:var(--ink);text-align:center;letter-spacing:.5px}
.about{position:absolute;left:0;top:340px;width:100%}
.about .section-title{border-bottom:1px solid var(--line);padding-bottom:8px;margin:0 20px}
.about-grid{display:flex;justify-content:space-between;padding:14px 40px 0}
.about-item{display:flex;gap:8px;width:140px}
.about-item svg{flex:none}
.about-item h3{font-size:10px;font-weight:500;color:var(--ink);margin-bottom:3px}
.about-item p{font-size:7px;line-height:1.4}
/* projects */
.projects{position:absolute;left:0;top:468px;width:100%;height:252px;background:var(--band);padding-top:16px}
.projects .section-title{color:#fff}
.project-grid{display:flex;justify-content:space-between;padding:16px 26px 0}
.project-card{width:206px;background:#fff;padding:7px}
.project-photo{height:104px}
.project-card h3{font-size:10px;font-weight:500;color:var(--ink);margin:7px 0 3px}
.project-card p{font-size:7px;line-height:1.4;margin-bottom:6px}
.more{font-size:7px;font-weight:700;color:var(--ink);text-decoration:none}
/* stories */
.stories{position:absolute;left:0;top:744px;width:100%;height:180px;display:flex;padding:0 10px;gap:16px}
.stories-col{flex:1}
.col-head{display:flex;justify-content:space-between;align-items:center;border-bottom:1px solid var(--line);padding-bottom:6px}
.col-head h2{font-size:12px;font-weight:500;text-transform:uppercase;color:var(--ink)}
.arrows{display:flex;gap:8px}
.story{display:flex;gap:8px;margin-top:12px}
.story-photo{width:60px;height:54px;flex:none}
.story h3{font-size:10px;font-weight:500;color:var(--ink);margin-bottom:3px}
.story p{font-size:7px;line-height:1.45;margin-bottom:3px}
.video{position:relative;margin-top:12px;height:120px;
  background:linear-gradient(90deg,#4f4034 0,#8a6a4a 30%,#b3834f 55%,#6e5844 80%,#3f3730 100%)}
.video svg{position:absolute;left:50%;top:50%;transform:translate(-50%,-50%)}
/* giving */
.support{position:absolute;left:10px;top:934px;width:701px;height:118px;display:flex;gap:12px}
.support-box{flex:1;border:1px solid var(--line);display:flex;gap:10px;padding:7px}
.support-photo{width:120px;flex:none;background:linear-gradient(160deg,#3a3a3a,#777 55%,#b9b9b9)}
.support-box h2{font-size:14px;font-weight:500;text-transform:uppercase;color:var(--ink);margin:4px 0 6px}
.support-box p{font-size:7.5px;line-height:1.5;margin-bottom:6px}
.volunteer{flex-direction:column;gap:0}
/* footer */
.site-footer{position:absolute;left:0;top:1064px;width:100%;height:136px;background:var(--soft);border-top:3px solid var(--dark);padding:16px 20px;display:flex;gap:30px}
.foot-brand{width:120px;display:flex;flex-direction:column;align-items:center}
.foot-brand .brand-mark{width:26px;height:26px}
.foot-brand .brand-name{font-size:12px}
.copyright{font-size:6.5px;line-height:1.5;text-align:center;margin-top:10px}
.site-footer h4{font-size:8px;font-weight:700;text-transform:uppercase;color:var(--ink);margin-bottom:8px}
.links{display:grid;grid-template-columns:70px 60px;row-gap:4px;font-size:7px}
.contact p{font-size:7px;line-height:1.6}
.newsletter{margin-left:auto;width:180px}
.signup{display:flex;gap:5px}
.signup span{flex:1;border:1px solid var(--line);background:#fff;font-size:7px;padding:5px;color:var(--mid)}
.signup b{background:var(--ink);color:#fff;font-size:7px;padding:5px 9px;border-radius:10px;font-weight:500;text-transform:uppercase}
</style>
</head>
<body>
<div class="page">
  <header class="site-header">
    <div class="brand"><span class="brand-mark"></span><span class="brand-name">MARIGOLD</span><span class="brand-sub">VENTURE</span></div>
    <nav class="main-nav">
      <a class="active">Home</a><a>About Marigold</a><a>Our Projects</a><a>News/Stories</a><a>Giving</a><a>Contact</a>
      <div class="social"><span></span><span></span><span></span></div>
    </nav>
  </header>

  <div class="hero" role="img" aria-label="Photo: a large group of village women and children standing together in bright clothing outside a building"></div>

  <section class="about">
    <h2 class="section-title">About Marigold</h2>
    <div class="about-grid">
      <div class="about-item"><svg width="18" height="18" viewBox="0 0 18 18"><circle cx="9" cy="9" r="8" fill="none" stroke="#1e1e1e" stroke-width="1.5"/><circle cx="9" cy="9" r="3" fill="#1e1e1e"/></svg><div><h3>Purpose</h3><p>Why we exist and the change we work toward.</p></div></div>
      <div class="about-item"><svg width="18" height="18" viewBox="0 0 18 18"><path d="M9 16 2 9a4 4 0 0 1 7-5 4 4 0 0 1 7 5z" fill="none" stroke="#1e1e1e" stroke-width="1.5"/></svg><div><h3>Values</h3><p>Respect, partnership and honesty guide our work.</p></div></div>
      <div class="about-item"><svg width="18" height="18" viewBox="0 0 18 18"><rect x="3" y="2" width="12" height="14" fill="none" stroke="#1e1e1e" stroke-width="1.5"/><path d="M6 6h6M6 9h6M6 12h4" stroke="#1e1e1e" stroke-width="1.2"/></svg><div><h3>Meaning of Name</h3><p>Why the marigold stands for hope and growth.</p></div></div>
      <div class="about-item"><svg width="18" height="18" viewBox="0 0 18 18"><circle cx="9" cy="6" r="3.5" fill="none" stroke="#1e1e1e" stroke-width="1.5"/><path d="M2 17a7 7 0 0 1 14 0" fill="none" stroke="#1e1e1e" stroke-width="1.5"/></svg><div><h3>Board</h3><p>Meet the trustees who steer our mission.</p></div></div>
    </div>
  </section>

  <section class="projects">
    <h2 class="section-title">Current Projects</h2>
    <div class="project-grid">
      <article class="project-card"><div class="project-photo" role="img" aria-label="Photo: children gathered outside a rural school" style="background:linear-gradient(180deg,#9aa08a 0,#6f7a5c 40%,#a67c52 75%,#7a5a3c 100%)"></div><h3>Lotus Path Cambodia</h3><p>Children's safe housing and schooling for rural families.</p><a class="more">Learn More</a></article>
      <article class="project-card"><div class="project-photo" role="img" aria-label="Photo: women's group meeting outdoors on red earth" style="background:linear-gradient(180deg,#6f7d52 0,#8c6a44 40%,#b5784a 75%,#8a5a36 100%)"></div><h3>Hillside Rwanda</h3><p>Women's self-help groups in rural villages building savings.</p><a class="more">Learn More</a></article>
      <article class="project-card"><div class="project-photo" role="img" aria-label="Photo: community members gathered beside a water tank" style="background:linear-gradient(180deg,#b7bec2 0,#8f9aa0 35%,#7a6248 70%,#5c4634 100%)"></div><h3>Clearwater Kenya</h3><p>Clean water wells for Maasai communities in the dry south.</p><a class="more">Learn More</a></article>
    </div>
  </section>

  <section class="stories">
    <div class="stories-col">
      <div class="col-head"><h2>Highlight Stories</h2><div class="arrows"><svg width="8" height="10" viewBox="0 0 8 10"><path d="M6 1 2 5l4 4" fill="none" stroke="#1e1e1e" stroke-width="1.6"/></svg><svg width="8" height="10" viewBox="0 0 8 10"><path d="m2 1 4 4-4 4" fill="none" stroke="#1e1e1e" stroke-width="1.6"/></svg></div></div>
      <div class="story"><div class="story-photo" role="img" aria-label="Photo: woman standing in front of her small shop" style="background:linear-gradient(150deg,#6b5640,#b88b5c)"></div><div><h3>A shop of her own</h3><p>A mother in Rwanda shares how her savings group helped her open a small shop and send her daughters to school.</p><a class="more">Learn More</a></div></div>
      <div class="story"><div class="story-photo" role="img" aria-label="Photo: children at a village water well" style="background:linear-gradient(150deg,#5e6a70,#a58a66)"></div><div><h3>Water close to home</h3><p>After the new well opened, children in the village now spend their mornings in class instead of carrying water.</p><a class="more">Learn More</a></div></div>
    </div>
    <div class="stories-col">
      <div class="col-head"><h2>Watch Stories</h2><div class="arrows"><svg width="8" height="10" viewBox="0 0 8 10"><path d="M6 1 2 5l4 4" fill="none" stroke="#1e1e1e" stroke-width="1.6"/></svg><svg width="8" height="10" viewBox="0 0 8 10"><path d="m2 1 4 4-4 4" fill="none" stroke="#1e1e1e" stroke-width="1.6"/></svg></div></div>
      <div class="video" role="img" aria-label="Video still: project participants seated together in a village">
        <svg width="30" height="30" viewBox="0 0 30 30"><circle cx="15" cy="15" r="14" fill="#1e1e1e" fill-opacity=".75"/><path d="M12 9v12l9-6z" fill="#fff"/></svg>
      </div>
    </div>
  </section>

  <section class="support">
    <div class="support-box">
      <div class="support-photo" role="img" aria-label="Black and white photo: hands holding a handwritten sign offering help"></div>
      <div><h2>Online Giving</h2><p>Your gift goes straight to our partners in the field. Choose a one-off or monthly gift and see where it is spent.</p><a class="more">Learn More</a></div>
    </div>
    <div class="support-box volunteer">
      <h2>Volunteer Vacancies</h2><p>We need people with skills in teaching, health and building. Find a role that fits your time and talents today.</p><a class="more">Learn More</a>
    </div>
  </section>

  <footer class="site-footer">
    <div class="foot-brand"><span class="brand-mark"></span><span class="brand-name">MARIGOLD</span><span class="brand-sub">VENTURE</span>
      <p class="copyright">Copyright © 2014 The Marigold Venture.<br>Terms &amp; Conditions | Privacy Policy | Sitemap</p></div>
    <div><h4>Quick Links</h4><div class="links"><span>Home</span><span>Giving</span><span>About Marigold</span><span>Contact</span><span>Our Projects</span><span></span><span>Stories</span></div></div>
    <div class="contact"><h4>Contact Us</h4><p>The Marigold Venture<br>PO Box 4821<br>Harrow Lane, Leeds<br>T: 0113 496 0234<br>E: hello@marigoldventure.org</p></div>
    <div class="newsletter"><h4>Newsletter Sign Up</h4><div class="signup"><span>Enter Email Address</span><b>Sign Up</b></div></div>
  </footer>
</div>
</body>
</html>
```